Stationery Set for Velmora Company

I need to create full stationery design for my company; Business Cards, Envelops, Letter Heads, Calendar.
In the letter head and Envelops... only contact information and website links.
Our company is a Service Management company with different domains of innovative services including Technology Service Management, Education Services, Outsourcing Management, Events Management.
I need a modern and innovative design specially for the business card. I some transparent designs and I like it, but don't limit your innovation to what I mentioned. Sky is limit for your innovation.

Target Market(s)

Middle East & Africa

Industry/Entity Type

Business Management

Colors
34a7d8
0355a3
85acd3
86cae7
cee9f5
cfdeed
e4daeb
f3f1f8
ecf7fb

Requirements
Must have
• Name, Title, Email, Mobile
Nice to have
• We have multiple locations in USA, KSA, EGY, so I need ideas about how to include all contact details maybe QR / Barcode or something else.
• Please see our locations and contact information: www.brightvelmora.example
Should not have
• Too much text

```html
<!DOCTYPE html>
<html lang="en">
<head>
<meta charset="utf-8">
<title>Velmora Company – Envelope</title>
<link rel="stylesheet" href="https://fonts.googleapis.com/css2?family=Quicksand:wght@500;700&family=Cairo:wght@700&display=swap">
<style>
  :root {
    --page: #ffffff;
    --paper: #ffffff;
    --edge: #9a9a9a;
    --brand-blue: #2f5cff;
    --text-blue: #2a4cff;
    --band-light: #d3defd;
    --band-mid: #2f62ff;
    --band-end: #9fb6ff;
    --deco-light: #e3f2fb;
    --deco-deep: #e2e7f5;
    --window-line: #555555;
  }
  html, body {
    margin: 0;
    width: 1200px;
    height: 1000px;
    overflow: hidden;
    background: var(--page);
  }
  .canvas {
    position: relative;
    width: 1200px;
    height: 1000px;
  }
  .envelope {
    position: absolute;
    left: 12px;
    top: 218px;
    width: 1174px;
    height: 587px;
    background: var(--paper);
    border-top: 1px solid var(--edge);
    box-shadow: -4px 4px 8px rgba(0,0,0,0.35);
    overflow: hidden;
  }
  .corner-decoration {
    position: absolute;
    left: 0;
    top: 25px;
    width: 490px;
    height: 320px;
    background: linear-gradient(160deg, var(--deco-light) 0%, var(--deco-deep) 60%, rgba(255,255,255,0) 100%);
  }
  .brand {
    position: absolute;
    left: 72px;
    top: 86px;
    display: flex;
    align-items: center;
    gap: 10px;
  }
  .brand-name {
    font-family: "Quicksand", sans-serif;
    font-weight: 700;
    font-size: 30px;
    line-height: 1;
    color: var(--brand-blue);
  }
  .brand-dot {
    width: 13px;
    height: 13px;
    border-radius: 50%;
    background: var(--brand-blue);
  }
  .tagline-ar {
    position: absolute;
    left: 73px;
    top: 163px;
    width: 268px;
    height: 27px;
    background: var(--brand-blue);
    color: #ffffff;
    font-family: "Cairo", sans-serif;
    font-weight: 700;
    font-size: 17px;
    line-height: 27px;
    text-align: center;
    direction: rtl;
  }
  .address {
    position: absolute;
    left: 74px;
    top: 208px;
    margin: 0;
    font-family: "Quicksand", sans-serif;
    font-weight: 500;
    font-size: 19px;
    line-height: 29.5px;
    color: var(--text-blue);
    font-style: normal;
  }
  .band {
    position: absolute;
    left: 0;
    top: 454px;
    width: 100%;
    height: 48px;
    background: linear-gradient(90deg, var(--band-light) 0%, var(--band-mid) 32%, var(--band-end) 100%);
    border-top: 2px solid #e6e6e6;
  }
  .address-window {
    position: absolute;
    left: 638px;
    top: 318px;
    width: 482px;
    height: 202px;
    background: var(--paper);
    border: 1px solid var(--window-line);
    border-radius: 14px;
    box-shadow: 0 0 0 2px #ffffff, 0 0 0 3px #bdbdbd;
  }
</style>
</head>
<body>
<div class="canvas">
  <section class="envelope">
    <div class="corner-decoration" role="img" aria-label="Soft blue decorative stripe pattern area"></div>

    <div class="brand">
      <span class="brand-name">Velmora Company</span>
      <span class="brand-dot"></span>
    </div>

    <div class="tagline-ar" lang="ar">حلول الخدمات الحديثة</div>

    <address class="address">
      118 Harbor Crest Lane, 4th<br>
      Floor Marlow Bay CA 90412<br>
      US
    </address>

    <div class="band"></div>
    <div class="address-window"></div>
  </section>
</div>
</body>
</html>
```